Landing Page / Waitlist

I would like a landing page for people to sign up for a waiting list. The text on the page should include (but is not limited to):
1) Main point: The accounting system you'll love
2) Secondary points:
a. Ruthlessly efficient
b. Quietly intelligent
c. Driven by AI
I've attached a file of our logo

The design should be simple, clean, and innovative - this is an ai company

```html
<!DOCTYPE html>
<html lang="en">
<head>
<meta charset="utf-8">
<title>Ledgerline — Join the Waitlist</title>
<link rel="stylesheet" href="https://fonts.googleapis.com/css2?family=Montserrat:wght@400;500;600;700;800&display=swap">
<style>
  :root {
    --night: #070a26;
    --deep: #0a1a45;
    --glow: #0d3a78;
    --violet: #120731;
    --accent: #16a8f0;
    --button: #05b4f5;
    --brand-grey: #8d9aa3;
    --white: #ffffff;
    --field-border: #c9d3dc;
    --placeholder: #7a7f86;
    --mesh: #134a9a;
  }
  * { box-sizing: border-box; margin: 0; padding: 0; }
  html, body { width: 1200px; height: 811px; overflow: hidden; }
  body {
    font-family: "Montserrat", Arial, sans-serif;
    color: var(--white);
    background: var(--night);
  }
  .page {
    position: relative;
    width: 1200px;
    height: 811px;
    overflow: hidden;
    background:
      radial-gradient(ellipse 520px 300px at 560px 180px, var(--glow) 0%, rgba(13,58,120,0.35) 45%, rgba(7,10,38,0) 100%),
      linear-gradient(100deg, var(--deep) 0%, var(--night) 55%, var(--violet) 100%);
  }
  .terrain {
    position: absolute;
    left: 0; right: 0;
    top: 400px;
    height: 330px;
    background:
      radial-gradient(ellipse 700px 120px at 600px 120px, rgba(19,74,154,0.55) 0%, rgba(19,74,154,0) 100%),
      linear-gradient(180deg, rgba(19,74,154,0) 0%, rgba(19,74,154,0.35) 35%, rgba(10,30,80,0.25) 70%, rgba(7,10,38,0) 100%);
  }
  .brand {
    position: absolute;
    top: 96px;
    left: 0; right: 0;
    text-align: center;
    font-size: 36px;
    font-weight: 600;
    letter-spacing: -0.5px;
    color: var(--brand-grey);
  }
  .headline {
    position: absolute;
    top: 198px;
    left: 0; right: 0;
    text-align: center;
    font-size: 46px;
    font-weight: 400;
    letter-spacing: 0.3px;
  }
  .headline strong { font-weight: 800; }
  .features {
    position: absolute;
    top: 314px;
    left: 0; right: 0;
    list-style: none;
  }
  .feature {
    position: absolute;
    top: 0;
    width: 220px;
    margin-left: -110px;
    text-align: center;
  }
  .feature-icon {
    width: 64px;
    height: 64px;
    margin: 0 auto;
    border-radius: 14px;
    background: radial-gradient(circle, rgba(22,168,240,0.55) 0%, rgba(22,168,240,0.15) 70%, rgba(22,168,240,0) 100%);
  }
  .feature-label {
    margin-top: 45px;
    font-size: 17.5px;
    font-weight: 500;
  }
  .signup {
    position: absolute;
    top: 515px;
    left: 373px;
    width: 454px;
  }
  .email-field {
    display: block;
    width: 454px;
    height: 51px;
    border-radius: 26px;
    border: 2px solid var(--field-border);
    background: var(--white);
    padding: 0 18px;
    font-family: inherit;
    font-size: 13.5px;
    color: #222;
  }
  .email-field::placeholder { color: var(--placeholder); }
  .join-button {
    display: block;
    margin: 24px auto 0;
    width: 204px;
    height: 40px;
    border: none;
    border-radius: 20px;
    background: var(--button);
    color: var(--white);
    font-family: inherit;
    font-size: 18px;
    font-weight: 600;
  }
  .footer {
    position: absolute;
    top: 746px;
    left: 0; right: 0;
    text-align: center;
    font-size: 14.5px;
    font-weight: 500;
  }
</style>
</head>
<body>
  <main class="page">
    <div class="terrain" role="img" aria-label="Glowing digital wireframe landscape with rising light particles"></div>

    <div class="brand">Ledgerline</div>

    <h1 class="headline"><strong>The accounting</strong> system you'll love</h1>

    <ul class="features">
      <li class="feature" style="left:348px">
        <div class="feature-icon" role="img" aria-label="Line icon of two figures in action, symbolising efficiency"></div>
        <p class="feature-label">Ruthlessly Efficient</p>
      </li>
      <li class="feature" style="left:600px">
        <div class="feature-icon" role="img" aria-label="Line icon of an AI gear with circuit connections"></div>
        <p class="feature-label">Quietly Intelligent</p>
      </li>
      <li class="feature" style="left:846px">
        <div class="feature-icon" role="img" aria-label="Line icon of an AI chip with circuit traces"></div>
        <p class="feature-label">Driven by AI</p>
      </li>
    </ul>

    <form class="signup">
      <input class="email-field" type="email" placeholder="Enter Your Email" aria-label="Email address">
      <button class="join-button" type="submit">Join the Waitlist</button>
    </form>

    <p class="footer">© 2025 Ledgerline. All rights reserved.</p>
  </main>
</body>
</html>
```